Brenton's Insurance Servives, Inc.

Full Service Insurance Broker.
Senior Health Care, Life, Annuity, Auto and Home
Specializing in Medicare Supplements. No cost, No Obligation Consulting.

Target Market(s)

General Public and senior citizens

Industry/Entity Type

Insurance Broker

Font styles to use
Decorative
Script

```html
<!DOCTYPE html>
<html lang="en">
<head>
<meta charset="utf-8">
<title>Brenton's Insurance Servives, Inc. – Medicare Supplements Banner</title>
<link href="https://fonts.googleapis.com/css2?family=Great+Vibes&family=Montserrat:wght@400;500;600;700;800&display=swap" rel="stylesheet">
<style>
  :root {
    --stage: #d6d6d6;
    --paper: #ffffff;
    --brand-blue: #1a7fc4;
    --sky-blue: #1e9be0;
    --navy: #1f2a6b;
    --ink: #1a1a1a;
    --photo-light: #dfe6d9;
    --photo-mid: #c9b8a8;
    --photo-warm: #e9c7b8;
    --photo-cool: #8fb4d8;
  }
  * { box-sizing: border-box; margin: 0; padding: 0; }
  html, body { width: 1200px; height: 733px; overflow: hidden; }
  body {
    background: var(--stage);
    font-family: "Montserrat", sans-serif;
    position: relative;
  }
  .banner {
    position: absolute;
    left: 0; top: 66px;
    width: 1200px; height: 600px;
    background: var(--paper);
    overflow: hidden;
  }
  .photo {
    position: absolute;
    left: 560px; top: 0;
    width: 640px; height: 600px;
    background:
      radial-gradient(ellipse 160px 220px at 220px 330px, var(--photo-warm), transparent 70%),
      radial-gradient(ellipse 170px 260px at 520px 370px, var(--photo-cool), transparent 70%),
      linear-gradient(180deg, var(--photo-light) 0%, #cfd8c4 45%, var(--photo-mid) 100%);
    -webkit-mask-image: linear-gradient(90deg, transparent 0%, #000 22%);
    mask-image: linear-gradient(90deg, transparent 0%, #000 22%);
  }
  .brand {
    position: absolute;
    left: 200px; top: 60px;
    display: flex; align-items: center; gap: 8px;
    font-weight: 600;
    font-size: 13px;
    color: var(--navy);
    white-space: nowrap;
  }
  .brand-dot {
    width: 14px; height: 14px; border-radius: 50%;
    background: var(--navy); flex: none;
  }
  .headline { position: absolute; left: 95px; top: 92px; width: 480px; height: 220px; }
  .headline-script {
    position: absolute; left: 0; top: 0;
    font-family: "Great Vibes", cursive;
    font-size: 112px; line-height: 1;
    color: var(--brand-blue);
  }
  .headline-main {
    position: absolute; left: 78px; top: 100px;
    font-weight: 700; font-size: 34px; line-height: 1.05;
    color: var(--ink); text-align: center;
  }
  .headline-swash { position: absolute; left: 0; top: 0; }
  .perks {
    position: absolute; left: 50px; top: 308px;
    display: flex; gap: 12px;
    font-size: 22px; font-weight: 500; color: var(--ink);
  }
  .perk { display: flex; align-items: center; gap: 6px; }
  .services {
    position: absolute; left: 19px; top: 356px;
    width: 584px; height: 150px;
    background: var(--brand-blue);
    border-radius: 70px;
    display: flex; justify-content: center; align-items: flex-start;
    padding: 14px 30px 0;
  }
  .service {
    width: 100px; text-align: center;
    color: #fff; font-weight: 600; font-size: 16px; line-height: 1.15;
    position: relative;
  }
  .service + .service::before {
    content: ""; position: absolute; left: 0; top: 20px;
    width: 1px; height: 88px; background: rgba(255,255,255,.7);
  }
  .service-icon {
    width: 80px; height: 80px; border-radius: 50%;
    background: #fff; margin: 0 auto 8px;
    display: flex; align-items: center; justify-content: center;
  }
  .call-bar {
    position: absolute; left: 17px; top: 505px;
    width: 586px; height: 50px;
    background: var(--navy);
    border-radius: 25px;
    display: flex; align-items: center; justify-content: center;
    font-weight: 700; font-size: 25px; color: #fff;
  }
  .call-bar .label { color: var(--sky-blue); margin-right: 8px; }
  .contact-line {
    position: absolute; left: 60px; top: 562px;
    display: flex; align-items: center; gap: 6px;
    font-size: 21px; font-weight: 500; color: var(--sky-blue); letter-spacing: 1.5px;
  }
  .contact-line .domain { color: var(--navy); font-weight: 600; }
</style>
</head>
<body>
<main class="banner">
  <div class="photo" role="img" aria-label="Photo of a smiling senior woman talking with a young insurance advisor on a sofa by a bright window"></div>

  <div class="brand"><span class="brand-dot"></span>Brenton's Insurance Servives, Inc.</div>

  <div class="headline">
    <svg class="headline-swash" width="480" height="230" viewBox="0 0 480 230" aria-hidden="true">
      <path d="M120 196 Q190 172 262 180" stroke="#1a1a1a" stroke-width="2" fill="none"/>
      <path d="M352 168 Q412 122 382 6" stroke="#1a7fc4" stroke-width="2" fill="none"/>
    </svg>
    <div class="headline-script">Specializing</div>
    <div class="headline-main">in Medicare<br>Supplements.</div>
  </div>

  <div class="perks">
    <span class="perk">
      <svg width="30" height="30" viewBox="0 0 30 30" aria-hidden="true"><circle cx="14" cy="15" r="12" fill="none" stroke="#1a7fc4" stroke-width="2"/><path d="M8 15 l5 5 L27 4" fill="none" stroke="#1a7fc4" stroke-width="3" stroke-linecap="round"/></svg>
      No cost,
    </span>
    <span class="perk">
      <svg width="30" height="30" viewBox="0 0 30 30" aria-hidden="true"><circle cx="14" cy="15" r="12" fill="none" stroke="#1a7fc4" stroke-width="2"/><path d="M8 15 l5 5 L27 4" fill="none" stroke="#1a7fc4" stroke-width="3" stroke-linecap="round"/></svg>
      No Obligation Consulting.
    </span>
  </div>

  <section class="services" aria-label="Services">
    <div class="service">
      <div class="service-icon"><svg width="46" height="46" viewBox="0 0 46 46" fill="none" stroke="#1f2a6b" stroke-width="2.5"><path d="M8 4 v12 a8 8 0 0 0 16 0 V4"/><path d="M16 24 v6 a9 9 0 0 0 18 0 v-4"/><circle cx="34" cy="22" r="4"/></svg></div>
      Senior Health Care
    </div>
    <div class="service">
      <div class="service-icon"><svg width="46" height="46" viewBox="0 0 46 46" fill="none" stroke="#1f2a6b" stroke-width="2.5"><path d="M23 24 C10 15 14 5 23 11 C32 5 36 15 23 24Z"/><path d="M4 22 l6 16 h10 M42 22 l-6 16 H26"/></svg></div>
      Life
    </div>
    <div class="service">
      <div class="service-icon"><svg width="46" height="46" viewBox="0 0 46 46" fill="none" stroke="#1f2a6b" stroke-width="2.5"><rect x="4" y="8" width="28" height="26" rx="2"/><path d="M4 15 h28 M11 4 v7 M25 4 v7"/><circle cx="33" cy="33" r="9" fill="#fff"/><path d="M33 28 v10"/></svg></div>
      Annuity
    </div>
    <div class="service">
      <div class="service-icon"><svg width="48" height="40" viewBox="0 0 48 40" fill="none" stroke="#1f2a6b" stroke-width="2.5"><path d="M6 20 l5 -12 h26 l5 12"/><rect x="3" y="20" width="42" height="12" rx="3"/><path d="M8 32 v5 M40 32 v5 M18 26 h12"/></svg></div>
      Auto
    </div>
    <div class="service">
      <div class="service-icon"><svg width="48" height="44" viewBox="0 0 48 44" fill="none" stroke="#1f2a6b" stroke-width="2.5"><path d="M3 20 L24 4 L45 20"/><rect x="8" y="18" width="32" height="22"/><rect x="20" y="28" width="8" height="12"/><rect x="12" y="23" width="6" height="6"/><rect x="30" y="23" width="6" height="6"/></svg></div>
      Home
    </div>
  </section>

  <div class="call-bar"><span class="label">Call us:</span>1-800-555-0142 and 412-555-0187</div>

  <div class="contact-line">
    <svg width="24" height="24" viewBox="0 0 24 24" aria-hidden="true"><circle cx="12" cy="12" r="10.5" fill="none" stroke="#1e9be0" stroke-width="1.5"/><path d="M8 7 l2 -1 2 3 -1.5 1.5 q1 2 3 3 l1.5 -1.5 3 2 -1 2 q-6 0 -9 -9z" fill="#1f2a6b"/></svg>
    <span>412-555-0163 |</span>
    <svg width="24" height="24" viewBox="0 0 24 24" aria-hidden="true" fill="none" stroke="#1f2a6b" stroke-width="1.5"><circle cx="12" cy="12" r="10"/><circle cx="12" cy="12" r="6.5"/><path d="M5.5 12 h13 M12 5.5 v13"/></svg>
    <span>www.<span class="domain">brenton-ins</span>.com</span>
  </div>
</main>
</body>
</html>
```